Business Card Design Project

We are a construction company in Orange County, CA. We need a two sided business card. We would like the back to be our logo with web URL. Front should included Name, title, address, phone, fax and email address.

our address is
627 West Dorrance Blvd, Suite 308
Anaheim, CA 92718

Our logo files are attached.

Construction

```html
<!DOCTYPE html>
<html lang="en">
<head>
<meta charset="utf-8">
<title>Kestran Business Card – Front and Back</title>
<link rel="stylesheet" href="https://fonts.googleapis.com/css2?family=Source+Sans+3:wght@400;700;900&display=swap">
<style>
  :root {
    --brand-blue: #1d4c7e;
    --accent-grey: #6b6b6d;
    --text-grey: #3c3c3e;
    --card-white: #ffffff;
    --backdrop: #ece7e1;
  }
  * { box-sizing: border-box; margin: 0; padding: 0; }
  html, body { width: 1200px; height: 402px; overflow: hidden; }
  body {
    background: var(--backdrop);
    font-family: "Source Sans 3", "Myriad Pro", Arial, sans-serif;
    position: relative;
  }
  .card {
    position: absolute;
    top: 60px;
    width: 512px;
    height: 291px;
    background: var(--card-white);
    overflow: hidden;
  }
  .card--front { left: 54px; }
  .card--back { left: 636px; }

  .wordmark {
    position: absolute;
    color: var(--brand-blue);
    font-weight: 900;
    line-height: 1;
    white-space: nowrap;
  }
  .card--front .wordmark { left: 22px; top: 118px; font-size: 50px; letter-spacing: -1px; }
  .card--back .wordmark { left: 0; right: 0; top: 98px; text-align: center; font-size: 94px; letter-spacing: -2px; }

  .accent-band {
    position: absolute;
    left: 266px;
    top: 0;
    width: 40px;
    height: 291px;
    background: linear-gradient(90deg, var(--brand-blue) 0%, var(--accent-grey) 50%, var(--brand-blue) 100%);
    opacity: 0.9;
  }
  .divider {
    position: absolute;
    left: 306px;
    right: 0;
    top: 189px;
    height: 2px;
    background: linear-gradient(90deg, rgba(107,107,109,0.2), var(--accent-grey));
  }

  .identity, .address, .contact-list {
    position: absolute;
    right: 22px;
    text-align: right;
    color: var(--text-grey);
  }
  .identity { top: 40px; }
  .identity__name { color: var(--brand-blue); font-weight: 700; font-size: 16px; line-height: 1.1; }
  .identity__title { font-size: 12px; line-height: 1.2; }

  .address { top: 128px; font-size: 12.5px; line-height: 1.25; font-style: normal; }

  .contact-list { top: 208px; list-style: none; font-size: 12.5px; line-height: 19px; }
  .contact-list li { display: flex; justify-content: flex-end; align-items: center; gap: 6px; }
  .contact-list svg { width: 10px; height: 10px; fill: var(--text-grey); }
</style>
</head>
<body>

<section class="card card--front" aria-label="Card front">
  <div class="accent-band" role="img" aria-label="Curved blue and grey stripe band"></div>
  <div class="divider"></div>

  <div class="wordmark">KESTRAN</div>

  <div class="identity">
    <p class="identity__name">Your name</p>
    <p class="identity__title">Title</p>
  </div>

  <address class="address">
    627 West Dorrance Blvd<br>
    Suite 308<br>
    Anaheim, CA&nbsp; 92718
  </address>

  <ul class="contact-list">
    <li><svg viewBox="0 0 10 10"><path d="M2 0.5 L3.8 2.8 L2.8 3.8 Q4 6 6.2 7.2 L7.2 6.2 L9.5 8 L8.3 9.5 Q3.5 9 0.5 1.7 Z"/></svg>01-555-0148</li>
    <li><svg viewBox="0 0 10 10"><path d="M2.5 0.5 H7.5 V3 H9.5 V7.5 H7.5 V9.5 H2.5 V7.5 H0.5 V3 H2.5 Z M3.3 6 V8.7 H6.7 V6 Z"/></svg>01-555-0148</li>
    <li><svg viewBox="0 0 10 10"><path d="M0.5 2 H9.5 V8.5 H0.5 Z"/><path d="M0.5 2 L5 5.5 L9.5 2" stroke="#fff" stroke-width="0.8" fill="none"/></svg>info@kestranbuild.com</li>
    <li><svg viewBox="0 0 10 10"><circle cx="5" cy="5" r="4.5"/><path d="M0.5 5 H9.5 M5 0.5 Q2.5 5 5 9.5 M5 0.5 Q7.5 5 5 9.5" stroke="#fff" stroke-width="0.7" fill="none"/></svg>www.kestranbuild.com</li>
  </ul>
</section>

<section class="card card--back" aria-label="Card back">
  <div class="wordmark">KESTRAN</div>
</section>

</body>
</html>
```